Business card, Invoice and printable service brochure

I need a 5.5x8.5 invoice, business card and printable service template for reception desk designed for my Rug repair, restoration and cleaning business.

I have included a picture for reference

www.velborenrug.example

Columns i need in my invoice:
Type of rug, Size, Background Color, Repair needs, Notes, Price and rug cleaning disclaimer.

Target Market(s)

Higher segment clients

Industry/Entity Type

Rug Repair, Restoration and cleaning,

Requirements
Must have
• Services hast to be listed on the invoice as well as service brochure.

```html
<!DOCTYPE html>
<html lang="en">
<head>
<meta charset="UTF-8">
<title>Velboren Rug — Business Card</title>
<link href="https://fonts.googleapis.com/css2?family=Cormorant+Garamond:wght@500&family=Open+Sans:wght@400;600&display=swap" rel="stylesheet">
<style>
  :root {
    --backdrop: #121212;
    --card: #262626;
    --gold: #d9b98a;
    --copper: #c48a5e;
    --pattern-dark: #2a1e16;
    --pattern-light: #a9704a;
  }
  * { box-sizing: border-box; margin: 0; padding: 0; }
  html, body {
    width: 1200px; height: 1200px; overflow: hidden;
    background: var(--backdrop);
  }
  .sheet {
    width: 1200px; height: 1200px;
    display: flex; flex-direction: column; align-items: center; justify-content: center;
    gap: 70px;
  }
  .card {
    position: relative;
    width: 720px; height: 411px;
    background: var(--card);
    overflow: hidden;
  }

  /* Front */
  .card-front {
    display: flex; flex-direction: column; align-items: center; justify-content: center;
  }
  .front-name {
    font-family: "Cormorant Garamond", Georgia, serif;
    font-weight: 500;
    font-size: 76px;
    letter-spacing: 1px;
    color: var(--gold);
    line-height: 1;
  }
  .front-tagline {
    margin-top: 10px;
    font-family: "Cormorant Garamond", Georgia, serif;
    font-weight: 500;
    font-size: 15px;
    letter-spacing: 6px;
    text-transform: uppercase;
    color: var(--copper);
  }

  /* Back */
  .card-back { display: flex; }
  .back-info {
    flex: 1;
    padding: 60px 0 0 58px;
    font-family: "Open Sans", Arial, sans-serif;
  }
  .back-name {
    font-weight: 600;
    font-size: 40px;
    letter-spacing: 0.5px;
    color: var(--gold);
    margin-bottom: 36px;
  }
  .contact-list { list-style: none; }
  .contact-item {
    display: flex; align-items: flex-start; gap: 22px;
    color: var(--copper);
    font-size: 25px; line-height: 1.2;
    margin-bottom: 20px;
  }
  .contact-icon { width: 24px; height: 24px; flex: none; margin-top: 4px; }
  .rug-panel {
    width: 236px; height: 100%;
    background: linear-gradient(135deg, var(--pattern-light) 0%, var(--pattern-dark) 45%, var(--pattern-light) 100%);
    border-left: 18px solid var(--copper);
  }
</style>
</head>
<body>
<main class="sheet">
  <section class="card card-front" aria-label="Card front">
    <h1 class="front-name">VELBOREN RUG</h1>
    <p class="front-tagline">Repair | Restoration | Cleaning</p>
  </section>

  <section class="card card-back" aria-label="Card back">
    <div class="back-info">
      <h2 class="back-name">VELBOREN RUG</h2>
      <ul class="contact-list">
        <li class="contact-item">
          <svg class="contact-icon" viewBox="0 0 24 24" fill="var(--gold)"><path d="M6.6 10.8a15.1 15.1 0 0 0 6.6 6.6l2.2-2.2a1 1 0 0 1 1-.25 11.4 11.4 0 0 0 3.6.57 1 1 0 0 1 1 1V20a1 1 0 0 1-1 1A17 17 0 0 1 3 4a1 1 0 0 1 1-1h3.5a1 1 0 0 1 1 1c0 1.25.2 2.45.57 3.57a1 1 0 0 1-.25 1z"/></svg>
          <span>(555)214-8630</span>
        </li>
        <li class="contact-item">
          <svg class="contact-icon" viewBox="0 0 24 24" fill="none" stroke="var(--gold)" stroke-width="1.5"><circle cx="12" cy="12" r="10"/><ellipse cx="12" cy="12" rx="4.5" ry="10"/><path d="M2 12h20M4 7h16M4 17h16"/></svg>
          <span>info@velborenrug.example</span>
        </li>
        <li class="contact-item">
          <svg class="contact-icon" viewBox="0 0 24 24" fill="none" stroke="var(--gold)" stroke-width="2"><path d="M12 22s7-7.2 7-12.5A7 7 0 0 0 5 9.5C5 14.8 12 22 12 22z"/><circle cx="12" cy="9.5" r="2.5"/></svg>
          <span>1820 Orchard Row,<br>Marlow, IL 60999</span>
        </li>
      </ul>
    </div>
    <div class="rug-panel" role="img" aria-label="Ornamental copper Persian rug corner with floral border and fringe"></div>
  </section>
</main>
</body>
</html>
```